Frostvale Harborline LLC

we need a business card design

Industry/Entity Type

hvac

Contact Information for Business Card

my logo

Requirements
Must have
• my logo and same colors

```html
<!DOCTYPE html>
<html lang="en">
<head>
<meta charset="utf-8">
<title>Frostvale Harborline LLC – Business Card</title>
<link href="https://fonts.googleapis.com/css2?family=Poppins:wght@400;500;600;700;800&display=swap" rel="stylesheet">
<style>
  :root{
    --stage:#2a2a2a;
    --card-blue:#1769b3;
    --card-blue-dark:#0f5ea6;
    --card-gold:#fcbd5b;
    --brand-blue:#1d63b8;
    --ink:#1c1c1c;
    --white:#ffffff;
  }
  *{box-sizing:border-box;margin:0;padding:0}
  html,body{width:1200px;height:800px;overflow:hidden}
  body{
    background:var(--stage);
    font-family:"Poppins",sans-serif;
    display:flex;align-items:center;justify-content:center;gap:48px;
  }
  .card{
    width:532px;height:304px;border-radius:18px;position:relative;overflow:hidden;
  }
  .card--front{
    background:radial-gradient(circle at 40% 30%, var(--card-blue) 0%, var(--card-blue-dark) 100%);
    display:flex;align-items:center;justify-content:center;
  }
  .brand{
    display:flex;align-items:center;gap:12px;
    font-weight:800;text-transform:uppercase;line-height:1.05;letter-spacing:.5px;
  }
  .brand__dot{width:22px;height:22px;border-radius:50%;flex:none}
  .card--front .brand{color:var(--white);font-size:30px}
  .card--front .brand__dot{background:var(--white)}
  .card--back{
    background:var(--card-gold);
    display:grid;grid-template-columns:230px 1fr;align-items:center;padding:0 30px 0 28px;
  }
  .card--back .brand{color:var(--brand-blue);font-size:20px;margin-top:70px}
  .card--back .brand__dot{background:var(--brand-blue);width:16px;height:16px}
  .contact__name{color:var(--brand-blue);font-weight:700;font-size:23px;line-height:1.1}
  .contact__role{color:var(--ink);font-weight:600;font-size:11.5px;text-transform:uppercase;margin:4px 0 20px}
  .contact__list{list-style:none}
  .contact__item{display:flex;align-items:flex-start;gap:10px;color:var(--ink);font-size:13px;line-height:1.35;margin-bottom:5px}
  .contact__icon{width:17px;height:17px;background:var(--brand-blue);border-radius:3px;flex:none;margin-top:1px}
</style>
</head>
<body>
  <section class="card card--front" aria-label="Card front">
    <div class="brand"><span class="brand__dot"></span><span>Frostvale<br>Harborline LLC</span></div>
  </section>

  <section class="card card--back" aria-label="Card back">
    <div class="brand"><span class="brand__dot"></span><span>Frostvale<br>Harborline LLC</span></div>
    <div class="contact">
      <h1 class="contact__name">Marcus Delaney</h1>
      <p class="contact__role">Managing Director</p>
      <ul class="contact__list">
        <li class="contact__item">
          <svg class="contact__icon" viewBox="0 0 17 17"><rect x="5" y="3" width="7" height="11" rx="1.2" fill="none" stroke="#fff" stroke-width="1.4"/><circle cx="8.5" cy="12" r=".8" fill="#fff"/></svg>
          <span>044-555 210 384</span>
        </li>
        <li class="contact__item">
          <svg class="contact__icon" viewBox="0 0 17 17"><path d="M3 8.5 14 3.5 11 14 8 10z" fill="#fff"/></svg>
          <span>info@frostvale.com</span>
        </li>
        <li class="contact__item">
          <svg class="contact__icon" viewBox="0 0 17 17"><circle cx="8.5" cy="8.5" r="5" fill="none" stroke="#fff" stroke-width="1.3"/><path d="M3.5 8.5h10M8.5 3.5c-2.5 3-2.5 7 0 10M8.5 3.5c2.5 3 2.5 7 0 10" fill="none" stroke="#fff" stroke-width="1"/></svg>
          <span>www.frostvalehvac.com</span>
        </li>
        <li class="contact__item">
          <svg class="contact__icon" viewBox="0 0 17 17"><path d="M8.5 14s-4-4.2-4-7a4 4 0 0 1 8 0c0 2.8-4 7-4 7z" fill="#fff"/><circle cx="8.5" cy="7" r="1.4" fill="#1d63b8"/></svg>
          <span>4471 Bayfront Coast Pkwy,<br>212- B, FL 32561</span>
        </li>
      </ul>
    </div>
  </section>
</body>
</html>
```